Information One Page for Email

I am looking for a informative attachment I can send with an introductive email for Meridale Slab Works. Something I can also Mail.

Meridale Slab Works is the leader in Rebar Post Tension Cable Placement and Post Tension Cable repair. Outside of cable placement and repair we do concrete repair, Parking Garage restoration and
Updates

Content

Post Tension Repair and Concrete Restoration
Post-tensioning is a revolutionary method in concrete construction that enhances the strength and durability of structures. However, like all construction ele-ments, post-tension cables can experience wear and damage over time. Ensuring timely and effective repair is crucial for maintaining the safety and integrity of your building.
Why Post-Tension Cable Repair is Essential
1. **Structural Integrity**: Damaged or deteriorated cables can compromise the structural integrity of your building, leading to safety hazards and potential structural failures.
2. **Extended Lifespan**: Regular maintenance and repair of post-tension cables extend the lifespan of your structure, ensuring it remains safe and function-al for years to come.
3. **Cost-Effective**: Addressing cable issues early on prevents more severe damage and costly repairs down the line.
Common Signs of Post-Tension Cable Issues
- Cracks in concrete surfaces
- Unusual noises or popping sounds
- Visible cable ends or broken strands
- Water leakage through cracks
Our Repair Process
1. **Inspection and Assessment**: Our team conducts a thorough inspection to identify the extent of the damage and determine the appropriate repair meth-ods.
2. **Cable Repair or Replacement**: Depending on the severity, we either re-pair the existing cables or replace them with new ones to restore full functional-ity.
3. **Sealing and Protection**: After repairing, we seal the affected areas to protect against moisture and future damage.
4. **Quality Assurance**: We perform rigorous quality checks to ensure the repairs meet industry standards and the structure is safe for use.
Why Choose Us
- **Expertise and Experience**: With years of experience in post-tension cable repair, our team is skilled in handling even the most complex repairs efficiently and effectively.
- **Advanced Technology**: We use the latest technology and materials to ensure durable and long-lasting repairs.
- **Customer Satisfaction**: Our commitment to quality and customer satisfaction sets us apart. We work closely with our clients to ensure their needs are met and expectations exceeded.
Contact Us
If you suspect issues with your post-tension cables or need a routine inspection, don't hesitate to contact us. Our experts are ready to provide the best solutions to keep your structures safe and secure.
Ensure the safety and longevity of your building with our professional post-tension cable repair services. Trust us to deliver quality and reliability every time.

```html
<!DOCTYPE html>
<html lang="en">
<head>
<meta charset="UTF-8">
<title>Meridale Slab Works – Post Tension Repair and Concrete Restoration</title>
<link href="https://fonts.googleapis.com/css2?family=Montserrat:wght@400;500;700;800&family=Oswald:wght@500;600&display=swap" rel="stylesheet">
<style>
  :root{
    --green:#0b6e3a;
    --green-deep:#075a2e;
    --ink:#444446;
    --grey:#4b4b4d;
    --grey-dark:#3a3a3c;
    --rule:#4a4a4a;
    --paper:#ffffff;
  }
  *{box-sizing:border-box;margin:0;padding:0}
  html,body{width:1200px;height:1159px;overflow:hidden}
  body{background:var(--paper);font-family:'Montserrat',sans-serif;color:var(--ink);position:relative}

  /* ---------- header ---------- */
  .masthead{position:relative;height:290px}
  .masthead-shape{position:absolute;inset:0}
  .masthead-copy{position:absolute;left:46px;top:52px;width:600px;color:#fff}
  .masthead-title{font-weight:800;font-size:33px;line-height:1.08;text-transform:uppercase;letter-spacing:.5px}
  .masthead-intro{margin-top:12px;font-size:13.5px;line-height:1.45;text-align:justify}
  .masthead-kicker{margin-top:6px;font-size:13.5px;font-weight:500}
  .brand{position:absolute;left:770px;top:110px;display:flex;align-items:center;gap:14px}
  .brand-mark{width:22px;height:22px;background:var(--green)}
  .brand-name{font-weight:700;font-size:38px;line-height:1;color:var(--green)}

  /* ---------- lists ---------- */
  .section{padding-left:60px;padding-right:60px}
  .items{list-style:none}
  .item{display:flex;gap:14px;align-items:flex-start;height:43px}
  .item-num{flex:0 0 30px;height:30px;border:2.5px solid var(--green);border-radius:50%;display:flex;align-items:center;justify-content:center;font-weight:800;font-size:15px;color:var(--ink);margin-top:2px}
  .item-title{font-weight:700;font-size:17px;color:var(--green);line-height:1.1}
  .item-text{font-size:12.5px;line-height:1.3;color:var(--ink)}
  .essentials{padding-top:12px}
  .signs{display:flex;gap:60px;margin-left:44px;margin-top:2px;font-size:12.5px;line-height:1.45}
  .signs-title{font-size:12.5px;margin-left:44px;margin-top:0}
  .signs ul{list-style:none}
  .signs li::before{content:"";display:inline-block;width:5px;height:5px;border-radius:50%;background:var(--ink);margin-right:6px;vertical-align:middle}

  /* ---------- section tabs ---------- */
  .tab{position:relative;height:44px;margin:6px 0 8px;display:flex;align-items:center}
  .tab-label{position:relative;z-index:1;height:40px;padding:0 48px 0 60px;background:var(--green);color:#fff;font-weight:800;font-size:25px;line-height:40px;text-transform:uppercase;letter-spacing:.5px;clip-path:polygon(0 0,100% 0,calc(100% - 22px) 100%,0 100%)}
  .tab-label.title-case{text-transform:none}
  .tab-tip{position:relative;width:30px;height:40px;margin-left:-26px;background:var(--grey-dark);clip-path:polygon(0 0,100% 0,calc(100% - 12px) 60%,0 100%)}
  .tab-rule{flex:1;height:1.5px;background:var(--rule);align-self:flex-start;margin-top:2px}

  /* ---------- contact ---------- */
  .contact{position:relative;height:80px}
  .contact-text{width:660px;font-size:12.5px;line-height:1.35}
  .phone{position:absolute;right:50px;top:-10px;display:flex;align-items:center;gap:12px}
  .phone-number{font-family:'Oswald',sans-serif;font-weight:600;font-size:50px;color:var(--grey-dark);letter-spacing:1px}

  .footer{position:absolute;left:0;bottom:0;width:1200px;height:118px}
  .footer-grey{position:absolute;right:0;bottom:0;width:560px;height:96px;background:var(--grey)}
  .footer-green{position:absolute;left:0;bottom:0;width:700px;height:118px;background:var(--green);clip-path:polygon(0 0,100% 0,92% 100%,0 100%)}
  .cta{position:absolute;left:110px;bottom:22px;font-family:'Oswald',sans-serif;font-weight:600;font-size:64px;line-height:1;color:#fff;text-transform:uppercase;letter-spacing:1px}
  .website{position:absolute;right:60px;bottom:32px;font-size:22px;font-weight:500;color:#fff;letter-spacing:.5px}
</style>
</head>
<body>

<header class="masthead">
  <svg class="masthead-shape" width="1200" height="290" viewBox="0 0 1200 290">
    <defs>
      <linearGradient id="panelTone" x1="0" y1="0" x2="1" y2="1">
        <stop offset="0" stop-color="#0e7a41"/>
        <stop offset="1" stop-color="#075a2e"/>
      </linearGradient>
    </defs>
    <path d="M0 0 H1200 V26 H700 V250 L676 290 H0 Z" fill="url(#panelTone)" role="img" aria-label="Green-toned photo of a post-tension slab under construction"/>
    <polyline points="1200,38 712,38 712,256 690,292" fill="none" stroke="#0b6e3a" stroke-width="1.5"/>
  </svg>
  <div class="masthead-copy">
    <h1 class="masthead-title">Post Tension Repair and<br>Concrete Restoration</h1>
    <p class="masthead-intro">Post-tensioning is a revolutionary method in concrete construction that enhances the strength and durability of structures. However, like all construction ele-ments, post-tension cables can experience wear and damage over time. Ensuring timely and effective repair is crucial for maintaining the safety and integrity of your building.</p>
    <p class="masthead-kicker">Why Post-Tension Cable Repair is Essential</p>
  </div>
  <div class="brand">
    <span class="brand-mark"></span>
    <span class="brand-name">Meridale Slab Works</span>
  </div>
</header>

<section class="section essentials">
  <ol class="items">
    <li class="item"><span class="item-num">1</span><div><h3 class="item-title">Structural Integrity :</h3><p class="item-text">Damaged or deteriorated cables can compromise the structural integrity of your building, leading to safety hazards and potential structural failures.</p></div></li>
    <li class="item"><span class="item-num">2</span><div><h3 class="item-title">Extended Lifespan :</h3><p class="item-text">Regular maintenance and repair of post-tension cables extend the lifespan of your structure, ensuring it remains safe and function-al for years to come.</p></div></li>
    <li class="item"><span class="item-num">3</span><div><h3 class="item-title">Cost-Effective :</h3><p class="item-text">Addressing cable issues early on prevents more severe damage and costly repairs down the line.</p></div></li>
  </ol>
  <p class="signs-title">Common Signs of Post-Tension Cable Issues</p>
  <div class="signs">
    <ul><li>Cracks in concrete surfaces</li><li>Unusual noises or popping sounds</li></ul>
    <ul><li>Visible cable ends or broken strands</li><li>Water leakage through cracks</li></ul>
  </div>
</section>

<div class="tab"><span class="tab-label">Our Repair Process</span><span class="tab-tip"></span><span class="tab-rule"></span></div>
<section class="section">
  <ol class="items">
    <li class="item"><span class="item-num">1</span><div><h3 class="item-title">Inspection and Assessment :</h3><p class="item-text">Our team conducts a thorough inspection to identify the extent of the damage and determine the appropriate repair meth-ods.</p></div></li>
    <li class="item"><span class="item-num">2</span><div><h3 class="item-title">Cable Repair or Replacement :</h3><p class="item-text">Depending on the severity, we either re-pair the existing cables or replace them with new ones to restore full functional-ity.</p></div></li>
    <li class="item"><span class="item-num">3</span><div><h3 class="item-title">Sealing and Protection :</h3><p class="item-text">After repairing, we seal the affected areas to protect against moisture and future damage.</p></div></li>
    <li class="item"><span class="item-num">4</span><div><h3 class="item-title">Quality Assurance :</h3><p class="item-text">We perform rigorous quality checks to ensure the repairs meet industry standards and the structure is safe for use.</p></div></li>
  </ol>
</section>

<div class="tab"><span class="tab-label title-case">Why Choose Us</span><span class="tab-tip"></span><span class="tab-rule"></span></div>
<section class="section">
  <ul class="items">
    <li class="item"><div><h3 class="item-title">Expertise and Experience :</h3><p class="item-text">With years of experience in post-tension cable repair, our team is skilled in handling even the most complex repairs efficiently and effectively.</p></div></li>
    <li class="item"><div><h3 class="item-title">Advanced Technology :</h3><p class="item-text">We use the latest technology and materials to ensure durable and long-lasting repairs.</p></div></li>
    <li class="item"><div><h3 class="item-title">Customer Satisfaction :</h3><p class="item-text">Our commitment to quality and customer satisfaction sets us apart. We work closely with our clients to ensure their needs are met and expectations exceeded.</p></div></li>
  </ul>
</section>

<div class="tab"><span class="tab-label title-case">Contact Us</span><span class="tab-tip"></span><span class="tab-rule"></span></div>
<section class="section contact">
  <p class="contact-text">If you suspect issues with your post-tension cables or need a routine inspection, don't hesitate to contact us. Our experts are ready to provide the best solutions to keep your structures safe and secure. Ensure the safety and longevity of your building with our professional post-tension cable repair services. Trust us to deliver quality and reliability every time.</p>
  <div class="phone">
    <svg width="46" height="46" viewBox="0 0 46 46" aria-hidden="true">
      <circle cx="23" cy="23" r="23" fill="#0b6e3a"/>
      <path d="M11 19 Q23 10 35 19 L32 23 L28 21 L28 18 Q23 16 18 18 L18 21 L14 23 Z" fill="#fff"/>
      <rect x="15" y="24" width="16" height="11" rx="2" fill="#fff"/>
      <circle cx="23" cy="29.5" r="3" fill="#0b6e3a"/>
    </svg>
    <span class="phone-number">(555) 014-2290</span>
  </div>
</section>

<footer class="footer">
  <div class="footer-grey"></div>
  <div class="footer-green"></div>
  <span class="cta">Contact Us Now</span>
  <span class="website">www.meridaleslabworks.com</span>
</footer>

</body>
</html>
```